Landing page design for my current website

I need a landing page designed for my Wordpress website. My website is Velmorquay.com, and I need a page that will serve as a landing page for online ads I run. Please follow the color scheme of the current website

This web page will be targeted towards real estate owners who are looking for a property manager. Above the fold needs to have a CTA form headlined with "As a Rental Property Owner, I Want More Protection, Less Stress, and Drama-Free Living"

A few highlights that can be listed beyond the CTA and fold

- Comprehensive Property Management
Full-service management covering tenant placement, leasing, maintenance, and inspections.

Maximized Rental Income
Proven strategies to optimize rental rates and minimize vacancies, ensuring higher ROI.

Stress-Free Management
We handle all tenant interactions, maintenance requests, and property issues, so you don't have to.

Experienced Team
Over a decade of experience in managing single-family homes, small multifamily units, and apartment complexes.

Advanced Technology
Utilize cutting-edge property management software for efficient communication, rent collection, and maintenance tracking.

Tenant Screening and Placement
Thorough background checks and tenant screening processes to ensure reliable and responsible tenants.

Regular Property Inspections
Routine inspections to maintain property condition and address issues before they become costly problems.

Legal Compliance
Expertise in local and federal rental laws to keep your properties compliant and avoid legal hassles.

Transparent Reporting
Detailed monthly reports and financial statements to keep you informed about your property's performance.

Personalized Service
Tailored management plans to meet the unique needs of your properties and investment goals.
Effective Tenant Conflict Resolution
Skilled in handling challenging tenant situations, ensuring conflicts are resolved quickly and professionally to maintain a peaceful living environment and protect your investment.

```html
<!DOCTYPE html>
<html lang="en">
<head>
<meta charset="utf-8">
<title>Velmorquay Realty – Property Management</title>
<link href="https://fonts.googleapis.com/css2?family=Montserrat:wght@600;700;800&family=Poppins:wght@400;500;600&display=swap" rel="stylesheet">
<style>
:root{
  --navy:#10457a;
  --blue:#0d68c8;
  --ink:#1c1c1c;
  --muted:#8f8f8f;
  --body:#4a4a4a;
  --line:#cfcfcf;
  --icon:#d9d9d9;
  --icon-active:#c5d3e3;
  --white:#ffffff;
}
*{box-sizing:border-box;margin:0;padding:0}
html,body{width:714px;height:1200px;overflow:hidden;background:var(--white);font-family:"Poppins",sans-serif;color:var(--ink)}
.page{position:relative;width:714px;height:1200px;overflow:hidden}
.top-rule{position:absolute;left:0;top:0;width:714px;height:3px;background:var(--blue)}
.call-pill{position:absolute;left:402px;top:0;width:276px;height:26px;background:var(--blue);border-radius:0 0 140px 140px/0 0 26px 26px;color:var(--white);font-size:10.5px;font-weight:500;text-align:center;line-height:23px}
.hero-photo{position:absolute;left:0;top:0;width:714px;height:358px;
  background:linear-gradient(180deg,#fbfbfb 0%,#f1f1f2 35%,#e7e1d8 55%,#cbc2b4 72%,#c9c7bd 84%,#b9c6a8 100%)}
.hero-veil{position:absolute;left:0;top:0;width:714px;height:358px;background:linear-gradient(180deg,rgba(255,255,255,.9) 0%,rgba(255,255,255,.55) 55%,rgba(255,255,255,.2) 100%)}
.brand{position:absolute;left:62px;top:27px;display:flex;align-items:center;gap:6px}
.brand-dot{width:22px;height:22px;border-radius:50%;border:2px solid var(--navy)}
.brand-name{font-family:"Montserrat",sans-serif;font-weight:700;font-size:12px;color:var(--navy);letter-spacing:.3px}
.nav{position:absolute;top:36px;left:305px;font-size:10px}
.nav a{color:var(--ink);text-decoration:none;position:absolute;white-space:nowrap}
.nav a.active{color:var(--blue);font-weight:500}
.hero-title{position:absolute;left:120px;top:119px;width:490px;text-align:center;font-family:"Montserrat",sans-serif;font-weight:800;font-size:21.3px;line-height:26.3px;color:var(--navy)}
.lead-frame{position:absolute;left:56px;top:326px;width:602px;height:255px;border:1px solid var(--navy)}
.lead-form{position:absolute;left:62px;top:331px;width:590px;height:245px;background:var(--navy)}
.field{position:absolute;background:var(--white);font-size:9.5px;color:var(--ink);padding:0 10px;display:flex;align-items:center}
.field.area{align-items:flex-start;padding-top:10px}
.submit{position:absolute;left:249px;top:195px;width:92px;height:28px;background:var(--blue);color:var(--white);font-family:"Montserrat",sans-serif;font-weight:700;font-size:10.5px;display:flex;align-items:center;justify-content:center;border-radius:2px}
.features{position:absolute;left:62px;top:650px;width:589px;height:430px;display:grid;grid-template-columns:196px 196px 197px;grid-template-rows:215px 215px;border-top:1px solid var(--line);border-left:1px solid var(--line)}
.feature{position:relative;border-right:1px solid var(--line);border-bottom:1px solid var(--line);text-align:center;background:var(--white)}
.feature.focus{box-shadow:0 4px 14px rgba(0,0,0,.28);z-index:2;border:none}
.icon-slot{position:absolute;left:60px;top:17px;width:76px;height:76px;border-radius:50%;background:var(--icon)}
.feature.focus .icon-slot{background:var(--icon-active)}
.feature h3{position:absolute;left:8px;right:8px;top:104px;font-family:"Montserrat",sans-serif;font-weight:700;font-size:12.5px;line-height:16.5px;color:var(--muted)}
.feature.focus h3{color:var(--navy)}
.feature p{position:absolute;left:18px;right:18px;top:142px;height:50px;overflow:hidden;font-size:9.3px;line-height:16.7px;color:var(--body)}
.feature p.low{top:150px}
.feature p.tech{top:126px}
.read-more{position:absolute;left:0;right:0;top:178px;font-size:9.5px;font-weight:600;color:var(--navy);text-decoration:underline}
.pager{position:absolute;top:1111px;left:338px;display:flex;gap:6px}
.pager span{width:9px;height:9px;border-radius:50%;background:var(--navy)}
.pager span.current{background:var(--white);border:1.5px solid var(--navy)}
.footer{position:absolute;left:0;top:1167px;width:714px;height:33px;background:var(--navy);color:var(--white);font-size:9.3px;text-align:center;line-height:33px}
</style>
</head>
<body>
<div class="page">
  <div class="hero-photo" role="img" aria-label="Photo of a two-storey suburban family home with garages and flowering trees"></div>
  <div class="hero-veil"></div>
  <div class="top-rule"></div>
  <div class="call-pill">Call Us Today! : 555.014.2290</div>

  <div class="brand"><span class="brand-dot"></span><span class="brand-name">VELMORQUAY REALTY</span></div>

  <nav class="nav">
    <a class="active" style="left:0">Home</a>
    <a style="left:58px">Residents</a>
    <a style="left:132px">Investors</a>
    <a style="left:203px">Communities</a>
    <a style="left:295px">Contact Us</a>
  </nav>

  <h1 class="hero-title">RENTAL PROPERTY OWNER, I WANT MORE PROTECTION, LESS STRESS, AND DRAMA-FREE LIVING</h1>

  <div class="lead-frame"></div>
  <form class="lead-form">
    <div class="field" style="left:13px;top:16px;width:183px;height:33px">First Name*</div>
    <div class="field" style="left:203px;top:16px;width:184px;height:33px">Last Name*</div>
    <div class="field" style="left:393px;top:16px;width:183px;height:33px">Phone Number*</div>
    <div class="field" style="left:13px;top:58px;width:215px;height:32px">Email Address*</div>
    <div class="field" style="left:234px;top:58px;width:342px;height:32px">Address*</div>
    <div class="field area" style="left:13px;top:99px;width:563px;height:78px">Message*</div>
    <div class="submit">SUBMIT</div>
  </form>

  <section class="features">
    <article class="feature">
      <div class="icon-slot" role="img" aria-label="Icon of an agent presenting a house"></div>
      <h3>Comprehensive Property Management</h3>
      <p>Full-service management covering tenant placement, leasing, maintenance, and inspections.</p>
    </article>
    <article class="feature">
      <div class="icon-slot" role="img" aria-label="Icon of a hand holding money"></div>
      <h3>Maximized<br>Rental Income</h3>
      <p>Proven strategies to optimize rental rates and minimize vacancies, ensuring higher ROI.</p>
    </article>
    <article class="feature">
      <div class="icon-slot" role="img" aria-label="Icon of a team under a gear"></div>
      <h3>Stress-Free<br>Management</h3>
      <p>We handle all tenant interactions, maintenance requests, and property issues, so you don't have to.</p>
    </article>
    <article class="feature">
      <div class="icon-slot" role="img" aria-label="Icon of a group of people"></div>
      <h3>Experienced Team</h3>
      <p class="low">Over a decade of experience in managing single-family homes, small multifamily units, and apartment complexes.</p>
    </article>
    <article class="feature focus">
      <div class="icon-slot" role="img" aria-label="Icon of a processor chip with a gear"></div>
      <h3>Advanced Technology</h3>
      <p class="tech">Utilize cutting-edge property management software for efficient communication, rent collection, and maintenance tracking.</p>
      <span class="read-more">Read More</span>
    </article>
    <article class="feature">
      <div class="icon-slot" role="img" aria-label="Icon of a hand holding a key"></div>
      <h3>Tenant Screening and Placement</h3>
      <p class="low">Thorough background checks and tenant screening processes to ensure reliable and responsible tenants.</p>
    </article>
  </section>

  <div class="pager"><span class="current"></span><span></span><span></span></div>

  <footer class="footer">Copyright © 2024 Velmorquay Realty</footer>
</div>
</body>
</html>
```